We need a business card design for a new company located in Missouri City, TX, entitled 'BrightPath Chiropractic & Holistic Center'. Our services include restoration of health and vitality, spinal exam, health assessment, dietary & fitness programs, lymphatic & therapeutic massage, detox & remineralize body wraps, far infrared sauna therapy

Industry/Entity Type

Business

Contact Information for Business Card

BrightPath Chiropractic & Holistic Center, Marlene Okafor LMT, 4215 Elm Ridge Rd., Suite 310, Missouri City, TX 77482, 281-555-0193

```html
<!DOCTYPE html>
<html lang="en">
<head>
<meta charset="utf-8">
<title>BrightPath Chiropractic &amp; Holistic Center – Business Card</title>
<link rel="stylesheet" href="https://fonts.googleapis.com/css2?family=Arimo&family=Crimson+Pro:wght@400;600&display=swap">
<style>
  :root {
    --brand-blue: #1f5a87;
    --brand-teal: #17a08c;
    --soft-teal: #9ccfc1;
    --ink: #141414;
    --paper: #ffffff;
    --backdrop: #e6e6e6;
  }
  * { box-sizing: border-box; margin: 0; padding: 0; }
  html, body {
    width: 1189px; height: 1200px; overflow: hidden;
    background: var(--backdrop);
  }
  .card {
    position: absolute; left: 140px; width: 917px; height: 524px;
    background: var(--paper);
    box-shadow: 0 6px 14px rgba(0,0,0,.25);
    overflow: hidden;
  }
  .card--front { top: 45px; }
  .card--back { top: 623px; }

  /* front */
  .brand {
    position: absolute; left: 0; width: 518px; top: 130px;
    text-align: center; color: var(--ink);
    font-family: "Crimson Pro", Georgia, serif; font-weight: 400;
  }
  .brand__dot {
    display: block; width: 64px; height: 64px; margin: 0 auto 40px;
    border-radius: 50%; background: var(--brand-teal);
  }
  .brand__name { font-size: 47px; line-height: 1; letter-spacing: .5px; }
  .brand__tagline { font-size: 30px; line-height: 1; margin-top: 14px; letter-spacing: 1px; }

  .divider {
    position: absolute; left: 517px; top: 53px; width: 3px; height: 378px;
    background: var(--ink);
  }
  .person { position: absolute; left: 559px; top: 74px; }
  .person__name {
    font-family: "Crimson Pro", Georgia, serif; font-weight: 600;
    font-size: 56px; line-height: 1; color: var(--brand-blue);
  }
  .person__title {
    font-family: "Arimo", Arial, sans-serif; font-size: 36px; line-height: 1;
    color: var(--ink); margin-top: 6px;
  }
  .contacts {
    position: absolute; left: 572px; top: 313px; list-style: none;
    font-family: "Arimo", Arial, sans-serif; font-size: 28px; color: var(--ink);
  }
  .contacts li { display: flex; align-items: center; height: 37px; }
  .contacts svg { width: 22px; height: 22px; margin-right: 9px; flex: none; }

  .rule {
    position: absolute; left: 0; right: 0; top: 455px; height: 3px;
    background: var(--brand-blue);
  }
  .address-band {
    position: absolute; left: 0; right: 0; top: 463px; height: 61px;
    background: var(--brand-teal); color: #fff;
    font-family: "Arimo", Arial, sans-serif; font-size: 25px;
    display: flex; align-items: center; padding-left: 27px; white-space: nowrap;
  }

  /* back */
  .services__heading {
    position: absolute; left: 56px; top: 38px;
    font-family: "Crimson Pro", Georgia, serif; font-weight: 600;
    font-size: 76px; line-height: 1; color: var(--ink);
  }
  .services__list {
    position: absolute; left: 56px; top: 196px; list-style: none;
    font-family: "Arimo", Arial, sans-serif; font-size: 28px; color: var(--ink);
  }
  .services__list li { height: 43px; display: flex; align-items: center; }
  .services__list li::before {
    content: "*"; color: var(--brand-teal); font-size: 40px; width: 36px;
    padding-left: 4px; line-height: 1; transform: translateY(8px);
  }
  .backdrop-mark {
    position: absolute; left: 470px; top: 110px; width: 380px; height: 380px;
    border-radius: 50%; background: var(--soft-teal); opacity: .45;
  }
</style>
</head>
<body>

<section class="card card--front" aria-label="Business card front">
  <div class="brand">
    <span class="brand__dot" aria-hidden="true"></span>
    <div class="brand__name">BrightPath</div>
    <div class="brand__tagline">Chiropractic &amp; Holistic Center</div>
  </div>

  <div class="divider" aria-hidden="true"></div>

  <div class="person">
    <div class="person__name">Daniel Harwick</div>
    <div class="person__title">CEO</div>
  </div>

  <ul class="contacts">
    <li>
      <svg viewBox="0 0 22 22" aria-hidden="true"><rect width="22" height="22" fill="var(--brand-blue)"/><path d="M7 4l3 3-2 2c1 2 3 4 5 5l2-2 3 3-2 3C10 18 4 12 4 6z" fill="#fff"/></svg>
      281-555-0193
    </li>
    <li>
      <svg viewBox="0 0 22 22" aria-hidden="true"><rect width="22" height="22" fill="var(--brand-blue)"/><rect x="4" y="6" width="14" height="10" fill="none" stroke="#fff" stroke-width="1.6"/><path d="M4 6l7 6 7-6" fill="none" stroke="#fff" stroke-width="1.6"/></svg>
      hi@brightpath.com
    </li>
    <li>
      <svg viewBox="0 0 22 22" aria-hidden="true"><rect width="22" height="22" fill="var(--brand-blue)"/><circle cx="11" cy="11" r="7" fill="none" stroke="#fff" stroke-width="1.6"/><path d="M4 11h14M11 4c-3 4-3 10 0 14M11 4c3 4 3 10 0 14" fill="none" stroke="#fff" stroke-width="1.2"/></svg>
      www.brightpath.com
    </li>
  </ul>

  <div class="rule" aria-hidden="true"></div>
  <div class="address-band">Marlene Okafor LMT, 4215 Elm Ridge Rd., Suite 310, Missouri City, TX 77482,</div>
</section>

<section class="card card--back" aria-label="Business card back">
  <div class="backdrop-mark" aria-hidden="true"></div>
  <h2 class="services__heading">services</h2>
  <ul class="services__list">
    <li>spinal exam</li>
    <li>health assessment</li>
    <li>dietary &amp; fitness programs</li>
    <li>far infrared sauna therapy</li>
    <li>restoration of health and vitality</li>
    <li>detox &amp; remineralize body wraps</li>
    <li>lymphatic &amp; therapeutic massage</li>
  </ul>
</section>

</body>
</html>
```